QHX Compliant Dietary Supplement Label for Nutritional Company

We are in need of a label for our line of 20+ dietary supplements that are specifically formulated to balance body chemistry and match the biochemical individuality of our users based on hair tissue mineral analysis.

We have a line of approximately 20 different dietary supplements that will require use of new label in both a small (90 capsule) and large (180 capsule) size. We will start with the initial label in which Product name, Supplement Facts, and Ingredient list will need to be modified for each particular product thereafter.

The label will be placed on a transparent blue bottle with the color of lid being decided after label design. We are open to a transparent light amber bottle with black lid but blue is our preference.

We would like the majority of the label to be blue. Solid blue, fading of blue to darker blue/black, or subtle background designs are welcome with involvement of white and hints of orange. We do not want pictorial images on the label.

Label size:
Small bottle (120cc): Label size ~ 2.25” x 5.875”
Large bottle (200cc): Label size ~ 2.75” x 7.625”

Front:
-Logo near top of label with product name and description in middle and capsule count near the bottom

Right Side:
-Supplement Facts: See current product image below in brief
-Ingredient list: See current product image below in brief
-Manufactured for: See image below (This is on the left side of our current bottle and would like it moved to the bottom of the right side)

Left side:
-Suggested use: See current product image below in brief
-Leave room for possible warning statement
-Leave room for possible lot number printing
-Keep out of the reach of children.

The first files below are our current supplement label with product information. This information is what is needed on the label and will likely need some adjustments as we are updating our line of supplements and changes in QHX requirements.

The following files are the logo files and color palette.

The remaining files are some designs we came across for inspiration.

Thank you.

Target Market(s)

Health Care Profressionals

Industry/Entity Type

Health Care and Nutrition

Requirements
Nice to have
• Product name needs to be on same line in all one color
Should not have
• Pictorial Images

```html
<!DOCTYPE html>
<html lang="en">
<head>
<meta charset="utf-8">
<title>ADRENIQ Adrenal Supplement Label</title>
<link href="https://fonts.googleapis.com/css2?family=Barlow+Condensed:ital,wght@1,700&family=Lato:wght@400;700;900&family=Montserrat:wght@300;400;600&display=swap" rel="stylesheet">
<style>
  :root {
    --navy-deep: #0e1836;
    --navy-mid: #1b2760;
    --royal: #2f3e9e;
    --facts-blue: #1f2a8c;
    --orange: #f07a23;
    --white: #ffffff;
    --logo-blue: #4a7fd0;
    --page: #ffffff;
  }
  * { box-sizing: border-box; margin: 0; padding: 0; }
  html, body { width: 1200px; height: 906px; overflow: hidden; background: var(--page); }
  .canvas { position: relative; width: 1200px; height: 906px; }

  .label {
    position: absolute; left: 40px; top: 238px; width: 1120px; height: 429px;
    background: linear-gradient(180deg, var(--navy-deep) 0%, var(--navy-mid) 55%, var(--royal) 100%);
    color: var(--white);
    font-family: "Montserrat", sans-serif;
    overflow: hidden;
    box-shadow: 2px 3px 6px rgba(0,0,0,.25);
  }

  /* left panel */
  .suggested-use {
    position: absolute; left: 31px; top: 27px; width: 273px;
    font-size: 15px; line-height: 1.3; padding-bottom: 12px;
    border-bottom: 2px solid var(--white);
  }
  .notice {
    position: absolute; left: 31px; top: 258px; width: 273px; height: 69px;
    background: var(--white); color: var(--facts-blue);
    border: 2px solid var(--orange); border-radius: 4px;
    font-size: 14.5px; line-height: 1.3; padding: 5px 12px;
  }
  .notice strong { font-weight: 600; }
  .print-field { position: absolute; left: 31px; width: 273px; font-size: 15px; display: flex; align-items: flex-end; }
  .print-field .rule { flex: 1; border-bottom: 1px solid var(--white); margin-left: 4px; height: 12px; }
  .lot { top: 349px; }
  .exp { top: 376px; }

  /* front panel */
  .brand {
    position: absolute; left: 372px; top: 84px; width: 170px;
    display: flex; align-items: center; gap: 8px;
    color: var(--logo-blue); font-size: 15px; font-weight: 400; letter-spacing: 2px;
  }
  .brand-dot { width: 14px; height: 14px; border-radius: 50%; background: var(--orange); flex: none; }
  .brand-name { line-height: 1.2; }

  .product-name {
    position: absolute; left: 372px; top: 162px;
    font-family: "Barlow Condensed", sans-serif; font-style: italic; font-weight: 700;
    font-size: 74px; line-height: 1; letter-spacing: 1px;
  }
  .product-desc {
    position: absolute; left: 374px; top: 240px;
    font-size: 23px; font-weight: 300; color: var(--orange); letter-spacing: 0.5px;
  }
  .count { position: absolute; left: 382px; top: 320px; text-align: center; }
  .count-number { font-size: 62px; font-weight: 300; line-height: 1; }
  .count-unit { font-size: 15px; font-weight: 400; }

  /* right panel */
  .facts {
    position: absolute; left: 815px; top: 33px; width: 274px; height: 305px;
    background: var(--white); color: var(--facts-blue);
    border: 2px solid var(--facts-blue);
    font-family: "Lato", sans-serif; padding: 2px 5px;
  }
  .facts-title { font-weight: 900; font-size: 25px; line-height: 1.1; }
  .facts-serving { font-weight: 700; font-size: 10.5px; line-height: 1.25; padding-bottom: 4px; border-bottom: 7px solid var(--facts-blue); }
  .facts table { width: 100%; border-collapse: collapse; font-size: 10px; line-height: 1.1; }
  .facts th { font-size: 7.5px; font-weight: 700; text-align: right; padding: 2px 0; border-bottom: 3px solid var(--facts-blue); line-height: 1; }
  .facts td { padding: 1px 0; border-bottom: 1px solid var(--facts-blue); vertical-align: bottom; }
  .facts td.amt, .facts td.dv { text-align: right; white-space: nowrap; }
  .facts td.amt { width: 48px; }
  .facts td.dv { width: 46px; }
  .facts .indent { padding-left: 10px; display: block; }
  .facts tr.group-end td { border-bottom: 5px solid var(--facts-blue); }
  .facts tr.last td { border-bottom: 5px solid var(--facts-blue); }
  .facts-foot { font-size: 10px; padding-top: 3px; }

  .other-ingredients { position: absolute; left: 809px; top: 343px; width: 290px; font-size: 10.5px; line-height: 1.15; }
  .distributor { position: absolute; left: 809px; top: 378px; width: 290px; font-size: 10.5px; line-height: 1.3; }
  .other-ingredients strong, .distributor strong { font-weight: 600; }
</style>
</head>
<body>
<div class="canvas">
  <section class="label" aria-label="ADRENIQ adrenal supplement bottle label">

    <div class="suggested-use">SUGGESTED USE: One capsule daily or as directed by a physician.</div>
    <div class="notice"><strong>NOTICE:</strong> It is advisable to keep this and all supplements out of the reach of children.</div>
    <div class="print-field lot">LOT #:<span class="rule"></span></div>
    <div class="print-field exp">EXP:<span class="rule"></span></div>

    <div class="brand"><span class="brand-dot"></span><span class="brand-name">VESTRA LABORATORIES</span></div>
    <h1 class="product-name">ADRENIQ</h1>
    <div class="product-desc">ADRENAL SUPPLEMENT</div>
    <div class="count"><div class="count-number">90</div><div class="count-unit">CAPSULES</div></div>

    <div class="facts">
      <div class="facts-title">Supplement Facts</div>
      <div class="facts-serving">Serving Size: 1 Capsule<br>Servings Per Container 90</div>
      <table>
        <thead>
          <tr><th></th><th>Amount Per<br>Serving</th><th>% Daily<br>Value</th></tr>
        </thead>
        <tbody>
          <tr><td>Vitamin C (as ascorbic acid)</td><td class="amt">100 mg</td><td class="dv">111%</td></tr>
          <tr><td>Vitamin B5<span class="indent">(as D-calcium pantothenate)</span></td><td class="amt">100 mg</td><td class="dv">2000%</td></tr>
          <tr><td>Magnesium (as magnesium amino<span class="indent">acid chelate)</span></td><td class="amt">5 mg</td><td class="dv">1%</td></tr>
          <tr><td>Zinc (as zinc amino acid chelate)</td><td class="amt">1 mg</td><td class="dv">9%</td></tr>
          <tr><td>Manganese (as manganese<span class="indent">amino acid chelate)</span></td><td class="amt">1 mg</td><td class="dv">43%</td></tr>
          <tr class="group-end"><td>Potassium (as potassium<span class="indent">amino acid chelate)</span></td><td class="amt">25 mg</td><td class="dv">1%</td></tr>
          <tr><td>Suprarenal (adrenal) powder (bovine)</td><td class="amt">100 mg</td><td class="dv">†</td></tr>
          <tr><td>Liver Powder, defatted (bovine)</td><td class="amt">45 mg</td><td class="dv">†</td></tr>
          <tr class="last"><td>Betain Hydrochloride</td><td class="amt">25 mg</td><td class="dv">†</td></tr>
        </tbody>
      </table>
      <div class="facts-foot">† Daily Value not established</div>
    </div>

    <p class="other-ingredients"><strong>Other Ingredients:</strong> Hypromellose (Vegetable Capsule), GrainFlo (R) (Organic Rice Fiber)</p>
    <p class="distributor"><strong>Distributed by:</strong> VESTRA LABORATORIES, INC.<br>Cedar Mesa, AZ 85999 USA</p>

  </section>
</div>
</body>
</html>
```